Zielgruppe
Wir betreiben eine Bäckerei mit Kaffeehaus als Nahversorger in A-3032 Tannwiesen. Das design soll natürlich unsere Kunden ansprechen.
Aufgabenstellung
Es wird ein neuer Schriftzug horizontal für das Sanierungsobjekt gesucht. Folgende Vorgaben sind wünschenswert:
Schriftzug - Außenbeschilderung;
Schriftzug -Cafe- linksbündig, Schriftzug -Kesselbrunn- mittig, Schriftzug -Bäckerei- rechstbündig. Die Außenbeschilderung soll ca. 5m lang und ca. 70cm hoch sein. Siehe auch Bestandsobjekt im Anhang. Vorraussetzung ist, das das Design auf ALU oder Plexiglas folierbar ist.
Familienwappen;
Eine Druckversion ist im Anhang ersichtlich, eine vereinfachte Darstellung wäre durchaus möglich durch etwa Konturen/ Linien etc..
Farben;
Am Foto ersichtlich die neue Farbe der Fassade links und rechts.
Banner für zwischen den Fenstern - vertikal;
1x Design für Bäckerei (Semmel/ Brötchen, Korb mit Gebäck, etc.), Schriftzug oben -Bäckerei-, Schriftzug unten -Kesselbrunn-.
1x Design für Cafe (Kaffeetasse, Cupcake, etc), Schriftzug oben -Cafe-, Schriftzug unten -Kesselbrunn-.
Designvorschlag; helle Schrift auf dunklem Hintergrund- weinrot, smaragtgrün, dunkelblau???
Natürlich sind auch alternative/ abweichende Vorschläge wünschenswert.
Wir freuen uns auf die Designs !!!

```html
<!DOCTYPE html>
<html lang="de">
<head>
<meta charset="utf-8">
<title>Kesselbrunn – Außenbeschilderung und Banner</title>
<link rel="stylesheet" href="https://fonts.googleapis.com/css2?family=Kaushan+Script&family=Cinzel:wght@400&family=Open+Sans:wght@400;600&display=swap">
<style>
  :root {
    --wine-red: #be1e2d;
    --white: #ffffff;
    --paper: #ffffff;
    --script-shadow: rgba(90, 0, 10, 0.55);
    --art-light: rgba(255, 255, 255, 0.22);
    --art-soft: rgba(255, 255, 255, 0.08);
  }
  * { margin: 0; padding: 0; box-sizing: border-box; }
  html, body { width: 1200px; height: 1200px; overflow: hidden; background: var(--paper); }
  .canvas { position: relative; width: 1200px; height: 1200px; background: var(--paper); }

  /* Horizontal facade sign */
  .facade-sign {
    position: absolute; left: 112px; top: 326px; width: 976px; height: 88px;
    background: var(--wine-red);
  }
  .facade-sign .frame {
    position: absolute; inset: 6px; border: 3px solid var(--white);
  }
  .facade-sign .script {
    position: absolute; font-family: "Kaushan Script", cursive; color: var(--white);
    text-shadow: 2px 2px 3px var(--script-shadow); line-height: 1; white-space: nowrap;
  }
  .facade-sign .script--cafe { left: 140px; top: 11px; font-size: 54px; }
  .facade-sign .script--baeckerei { right: 133px; top: 18px; font-size: 48px; }
  .facade-sign .brand-name {
    position: absolute; left: 0; right: 0; top: 19px; text-align: center;
    font-family: "Cinzel", serif; font-size: 46px; line-height: 1; color: var(--white);
    letter-spacing: 1.5px; white-space: nowrap;
  }

  /* Vertical banners */
  .banner {
    position: absolute; top: 445px; width: 256px; height: 558px;
    background: var(--wine-red); color: var(--white); text-align: center;
  }
  .banner--baeckerei { left: 328px; }
  .banner--cafe { left: 613px; }
  .banner .frame {
    position: absolute; left: 14px; top: 14px; right: 14px; bottom: 14px;
    border: 2px solid var(--white);
  }
  .banner .base-line {
    position: absolute; left: 10px; right: 10px; bottom: 9px; height: 1px;
    background: rgba(255,255,255,0.45);
  }
  .banner .title {
    position: absolute; left: 0; right: 0; font-family: "Kaushan Script", cursive;
    font-weight: 400; line-height: 1; text-shadow: 2px 2px 3px var(--script-shadow);
    white-space: nowrap;
  }
  .banner--baeckerei .title { top: 26px; font-size: 50px; }
  .banner--cafe .title { top: 14px; font-size: 66px; }
  .banner .artwork {
    position: absolute; display: block;
    background: radial-gradient(ellipse at center, var(--art-light), var(--art-soft) 70%, transparent);
  }
  .banner--baeckerei .artwork { left: 23px; top: 182px; width: 211px; height: 105px; }
  .banner--cafe .artwork { left: 55px; top: 145px; width: 146px; height: 150px; }
  .banner .brand-name {
    position: absolute; left: 0; right: 0; top: 344px;
    font-family: "Cinzel", serif; font-size: 19px; line-height: 1; white-space: nowrap;
  }
  .banner .tagline {
    position: absolute; left: 0; right: 0; top: 370px;
    font-family: "Open Sans", sans-serif; font-size: 10.5px; line-height: 13.5px;
    letter-spacing: 0.3px;
  }
  .banner .crest {
    position: absolute; left: 85px; top: 406px; width: 84px; height: 96px;
    background: radial-gradient(ellipse at center, var(--art-light), var(--art-soft) 70%, transparent);
  }
  .banner .crest-note {
    position: absolute; left: 0; right: 0; top: 508px;
    font-family: "Open Sans", sans-serif; font-weight: 600; font-size: 7px; line-height: 1;
  }
</style>
</head>
<body>
<main class="canvas">

  <section class="facade-sign" aria-label="Außenbeschilderung">
    <div class="frame"></div>
    <span class="script script--cafe">Cafe</span>
    <span class="brand-name">KESSELBRUNN</span>
    <span class="script script--baeckerei">Bäckerei</span>
  </section>

  <section class="banner banner--baeckerei" aria-label="Banner Bäckerei">
    <div class="frame"></div>
    <div class="base-line"></div>
    <h2 class="title">Bäckerei</h2>
    <svg class="artwork" role="img" aria-label="Illustration: Brotlaib im Kreis mit Ährenkranz" viewBox="0 0 211 105"></svg>
    <p class="brand-name">KESSELBRUNN</p>
    <p class="tagline">DIE BACKEREI IN<br>TANNWIESEN</p>
    <svg class="crest" role="img" aria-label="Familienwappen" viewBox="0 0 84 96"></svg>
    <p class="crest-note">FAMILIENWAPPEN SEIT 1412</p>
  </section>

  <section class="banner banner--cafe" aria-label="Banner Cafe">
    <div class="frame"></div>
    <div class="base-line"></div>
    <h2 class="title">Cafe</h2>
    <svg class="artwork" role="img" aria-label="Illustration: dampfende Kaffeetasse mit Kaffeebohnen" viewBox="0 0 146 150"></svg>
    <p class="brand-name">KESSELBRUNN</p>
    <p class="tagline">DIE BACKEREI IN<br>TANNWIESEN</p>
    <svg class="crest" role="img" aria-label="Familienwappen" viewBox="0 0 84 96"></svg>
    <p class="crest-note">FAMILIENWAPPEN SEIT 1412</p>
  </section>

</main>
</body>
</html>
```